VOMRA Pty Ltd Business Card

Looking for a simple yet eye-catching double-sided business card design using my company logo on one side and contact details on the other.

Target Market(s)

Government

Industry/Entity Type

Communication Systems Engineering

Contact Information for Business Card

VOMRA Pty Ltd

Requirements
Nice to have
• Would be great to have a QR code so details can be scanned into contacts

```html
<!DOCTYPE html>
<html lang="en">
<head>
<meta charset="utf-8">
<title>VOMRA Pty Ltd Business Card</title>
<link href="https://fonts.googleapis.com/css2?family=Open+Sans:wght@400;700&display=swap" rel="stylesheet">
<style>
  :root {
    --backdrop: #232323;
    --card: #37424a;
    --ink: #ffffff;
    --mark: #56636c;
  }
  * { box-sizing: border-box; margin: 0; padding: 0; }
  html, body { width: 1200px; height: 780px; overflow: hidden; background: var(--backdrop); }
  body {
    font-family: "Open Sans", sans-serif;
    display: flex; align-items: center; justify-content: center; gap: 70px;
  }
  .card {
    position: relative;
    width: 340px; height: 570px;
    background: var(--card);
    color: var(--ink);
    overflow: hidden;
  }
  .card-back { border-radius: 150px 0 150px 0; }
  .card-front { border-radius: 0 150px 0 150px; }
  /* back side */
  .back-brand {
    position: absolute; left: 50%; top: 215px;
    transform: translate(-50%, -50%) rotate(90deg);
    white-space: nowrap;
    font-weight: 700; font-size: 80px; letter-spacing: 6px; line-height: 1;
    color: var(--mark);
  }
  .back-dot {
    position: absolute; left: 50%; bottom: 90px; transform: translateX(-50%);
    width: 70px; height: 70px; border-radius: 50%; background: var(--mark);
  }
  /* front side */
  .brand {
    position: absolute; left: 40px; top: 64px;
    display: flex; align-items: center; gap: 16px;
  }
  .brand-dot { width: 46px; height: 46px; border-radius: 50%; background: var(--ink); }
  .brand-name { font-weight: 700; font-size: 46px; letter-spacing: 4px; }
  .contact {
    position: absolute; left: 40px; right: 30px; top: 300px;
    text-align: center;
  }
  .person { font-weight: 700; font-size: 25px; line-height: 1.1; }
  .role { font-size: 14px; margin-bottom: 12px; }
  .icons { display: flex; justify-content: center; gap: 8px; margin-bottom: 6px; }
  .icon {
    width: 24px; height: 24px; border-radius: 50%; background: var(--ink);
    display: flex; align-items: center; justify-content: center;
  }
  .icon svg { width: 14px; height: 14px; }
  .lines { font-size: 14px; line-height: 1.35; }
  .pin { margin: 12px auto 6px; }
  .address { font-size: 14px; line-height: 1.35; }
</style>
</head>
<body>
  <section class="card card-back" aria-label="Card back">
    <div class="back-brand">VOMRA</div>
    <div class="back-dot"></div>
  </section>

  <section class="card card-front" aria-label="Card front">
    <div class="brand">
      <span class="brand-dot"></span>
      <span class="brand-name">VOMRA</span>
    </div>
    <div class="contact">
      <p class="person">Jordan Ellis</p>
      <p class="role">Co-Founder</p>
      <div class="icons">
        <span class="icon"><svg viewBox="0 0 24 24"><path fill="#37424a" d="M6.6 10.8a15 15 0 0 0 6.6 6.6l2.2-2.2c.3-.3.7-.4 1-.2 1.1.4 2.3.6 3.6.6.6 0 1 .4 1 1V20c0 .6-.4 1-1 1A17 17 0 0 1 3 4c0-.6.4-1 1-1h3.5c.6 0 1 .4 1 1 0 1.3.2 2.5.6 3.6.1.3 0 .7-.2 1z"/></svg></span>
        <span class="icon"><svg viewBox="0 0 24 24"><path fill="#37424a" d="M3 5h18v14H3zm2 2v.5l7 4.5 7-4.5V7l-7 4.5z"/></svg></span>
        <span class="icon"><svg viewBox="0 0 24 24"><circle cx="12" cy="12" r="9" fill="none" stroke="#37424a" stroke-width="2"/><path d="M3 12h18M12 3c3 3 3 15 0 18M12 3c-3 3-3 15 0 18" fill="none" stroke="#37424a" stroke-width="1.6"/></svg></span>
      </div>
      <p class="lines">(02) 5550 1834<br>www.vomra.com.au<br>admin@vomra.com.au</p>
      <span class="icon pin"><svg viewBox="0 0 24 24"><path fill="#37424a" d="M12 2a7 7 0 0 0-7 7c0 5 7 13 7 13s7-8 7-13a7 7 0 0 0-7-7zm0 9.5A2.5 2.5 0 1 1 12 6.5a2.5 2.5 0 0 1 0 5z"/></svg></span>
      <p class="address">14-16 Harlow Lane Redfern<br>NSW 2016 Australia</p>
    </div>
  </section>
</body>
</html>
```